Stationery Design Project

I need a stationary design for our company. we are based in Houston, TX and we are called Mira Vell Lending. And we are wanting to brand our MoneyMendPlus program, which includes our tax preparation and restoration, credit repair service. Although our business offers other programs, we are interested in mainly focusing on The MoneyMendPlus program. We are looking for way to brand our ourselves and I believe that a great stationery design will help in achieving this goal. Our logo design is blue and light blue. the slogan is orange.

Industry/Entity Type

Business

Requirements
Must have
• Address: 30871 Calloway Ln. B-22
Houston, TX 75419
Tel. 555-318-6207
Fax 555-294-7153
www.miravelllending.example
info@miravelllending.example
Our Slogan: Happiness, Restored!

```html
<!DOCTYPE html>
<html lang="en">
<head>
<meta charset="utf-8">
<title>Mira Vell Lending – MoneyMendPlus Business Card</title>
<link rel="stylesheet" href="https://fonts.googleapis.com/css2?family=Tinos:wght@400;700&family=Didact+Gothic&display=swap">
<style>
  :root {
    --stage: #ecebe8;
    --card-white: #ffffff;
    --navy: #1d4c86;
    --navy-deep: #143a6b;
    --sky: #1f8cc8;
    --orange: #f6a023;
    --text-light: #ffffff;
    --back-center: #2d80c4;
    --back-edge: #113766;
  }
  * { box-sizing: border-box; margin: 0; padding: 0; }
  html, body { width: 1200px; height: 724px; overflow: hidden; }
  body {
    background: var(--stage);
    position: relative;
    font-family: "Didact Gothic", "Century Gothic", sans-serif;
  }
  .card {
    position: absolute;
    top: 207px;
    width: 540px;
    height: 310px;
    overflow: hidden;
    box-shadow: 0 6px 18px rgba(0,0,0,0.18);
  }

  /* ---------- Front ---------- */
  .card-front { left: 40px; background: var(--card-white); }
  .front-brand {
    position: absolute;
    left: 34px;
    top: 96px;
    font-family: "Tinos", "Times New Roman", serif;
    font-size: 46px;
    color: var(--navy);
    letter-spacing: -0.5px;
  }
  .partner-mark {
    position: absolute;
    right: 34px;
    top: 22px;
    width: 112px;
    height: 112px;
    background: var(--navy);
    border: 4px solid #cfe0ef;
    display: flex;
    align-items: flex-end;
    justify-content: center;
    padding-bottom: 16px;
  }
  .partner-name {
    font-family: "Tinos", "Times New Roman", serif;
    font-size: 12px;
    color: var(--text-light);
  }
  .slogan-band {
    position: absolute;
    left: 0; right: 0;
    top: 176px;
    height: 30px;
    background: var(--orange);
    display: flex;
    align-items: center;
    justify-content: center;
  }
  .slogan {
    font-family: "Tinos", "Times New Roman", serif;
    font-weight: 700;
    font-size: 17px;
    letter-spacing: 2px;
    color: var(--text-light);
  }
  .contact-band {
    position: absolute;
    left: 0; right: 0;
    top: 206px;
    height: 34px;
    background: var(--sky);
    display: flex;
    align-items: center;
    justify-content: center;
    gap: 18px;
    color: var(--text-light);
    font-size: 13.5px;
  }
  .address-band {
    position: absolute;
    left: 0; right: 0;
    top: 240px;
    bottom: 0;
    background: var(--navy);
    color: var(--text-light);
    text-align: center;
    padding-top: 10px;
  }
  .contact-item { display: inline-flex; align-items: center; gap: 5px; }
  .icon { width: 12px; height: 12px; fill: var(--text-light); }
  .web-line {
    display: inline-flex; align-items: center; gap: 6px;
    font-size: 13.5px; letter-spacing: 1.6px;
  }
  .street-line { margin-top: 6px; font-size: 14.5px; letter-spacing: 0.6px; }

  /* ---------- Back ---------- */
  .card-back {
    left: 620px;
    background: radial-gradient(ellipse at 55% 40%, var(--back-center) 0%, var(--navy) 55%, var(--back-edge) 100%);
  }
  .back-frame {
    position: absolute;
    left: 190px;
    top: 56px;
    width: 190px;
    height: 190px;
    border: 6px solid rgba(255,255,255,0.09);
  }
  .back-brand {
    position: absolute;
    left: 0; right: 0;
    top: 112px;
    text-align: center;
    font-family: "Tinos", "Times New Roman", serif;
    font-size: 58px;
    color: var(--text-light);
    letter-spacing: -0.5px;
  }
  .back-partner {
    position: absolute;
    left: 0; right: 0;
    top: 184px;
    text-align: center;
    font-family: "Tinos", "Times New Roman", serif;
    font-weight: 700;
    font-size: 22px;
    color: rgba(255,255,255,0.12);
  }
  .back-web {
    position: absolute;
    left: 0; right: 0;
    top: 232px;
    text-align: center;
    font-family: "Tinos", "Times New Roman", serif;
    font-size: 13px;
    letter-spacing: 3px;
    color: var(--text-light);
  }
</style>
</head>
<body>

<section class="card card-front" aria-label="Business card front">
  <div class="front-brand">MoneyMendPlus</div>
  <div class="partner-mark"><span class="partner-name">Mira Vell Lending</span></div>

  <div class="slogan-band"><span class="slogan">HAPPINESS, RESTORED!</span></div>

  <div class="contact-band">
    <span class="contact-item">
      <svg class="icon" viewBox="0 0 12 12" aria-hidden="true"><path d="M2.5 1 L4.5 1 L5.2 3.4 L4 4.4 Q5 6.8 7.6 8 L8.6 6.8 L11 7.5 L11 9.5 Q10.5 11 9 11 Q1 10 1 2.6 Q1 1.2 2.5 1 Z"/></svg>
      555-318-6207
    </span>
    <span class="contact-item">
      <svg class="icon" viewBox="0 0 12 12" aria-hidden="true"><rect x="3" y="1" width="6" height="4"/><rect x="0.5" y="5" width="11" height="5" rx="1"/><rect x="3" y="8" width="6" height="3" fill="#1f8cc8"/></svg>
      555-294-7153
    </span>
    <span class="contact-item">
      <svg class="icon" viewBox="0 0 12 12" aria-hidden="true"><rect x="0.5" y="2" width="11" height="8" rx="1"/><path d="M1 2.6 L6 6.6 L11 2.6" stroke="#1f8cc8" stroke-width="1.2" fill="none"/></svg>
      info@miravelllending.example
    </span>
  </div>

  <div class="address-band">
    <div class="web-line">
      <svg class="icon" viewBox="0 0 12 12" aria-hidden="true"><circle cx="6" cy="6" r="5.5"/><path d="M0.5 6 H11.5 M6 0.5 V11.5 M6 0.5 Q2.5 6 6 11.5 M6 0.5 Q9.5 6 6 11.5" stroke="#1d4c86" stroke-width="0.9" fill="none"/></svg>
      www.miravelllending.example
    </div>
    <div class="street-line">30871 Calloway Ln. B-22, Houston, TX 75419</div>
  </div>
</section>

<section class="card card-back" aria-label="Business card back">
  <div class="back-frame"></div>
  <div class="back-brand">MoneyMendPlus</div>
  <div class="back-partner">Mira Vell Lending</div>
  <div class="back-web">www.miravelllending.example</div>
</section>

</body>
</html>
```